Rebrand stationary with recently completed logo design

Need new business cards, thank you cards, letterhead, envelopes and presentation folders. The designs will be sent to a separate production firm so I need the files to be print ready.

My contact info
Reko Haliburn

Office 604-318-5047
Fax 604-371-8054

Email reko@glazemark.ca
website www.glazemark.ca

315-14720 62nd Avenue,
Langley, BC, V2K 3R8

Target Market(s)

Homeowners, businesses and contractors

Industry/Entity Type

Business

Font styles to use
Sans Serif

Colors
34a7d7

Requirements
Must have
• Like to have one side of the business card a solid color with the logo in all white. The side with all the text to be a white background
• I find the current blue on the front of the card with the white logo too dark.
Should not have
• Gradient colors

```html
<!DOCTYPE html>
<html lang="en">
<head>
<meta charset="utf-8">
<title>Glazemark Presentation Folder</title>
<link rel="stylesheet" href="https://fonts.googleapis.com/css2?family=Arimo:ital,wght@0,400;0,700;1,400&display=swap">
<style>
  :root {
    --page-grey: #e6e7e8;
    --folder-blue: #0e90db;
    --folder-white: #ffffff;
    --body-on-blue: #dcefff;
    --frame-line: #5a5a5a;
    --brand-blue: #1a8fd0;
    --photo-tone-a: #9aa6ad;
    --photo-tone-b: #c9d0d3;
  }
  * { margin: 0; padding: 0; box-sizing: border-box; }
  html, body { width: 1200px; height: 882px; overflow: hidden; }
  body {
    background: var(--page-grey);
    font-family: "Arimo", Arial, sans-serif;
    position: relative;
  }
  .folder {
    position: absolute; left: 58px; top: 54px;
    width: 1090px; height: 772px;
    border: 1px solid var(--frame-line);
    background: var(--folder-white);
    overflow: hidden;
  }
  .inside-panel {
    position: absolute; left: 0; top: 0;
    width: 544px; height: 100%;
    background: var(--folder-blue);
    border-right: 1px solid var(--frame-line);
  }
  .feature {
    position: absolute; width: 181px; color: var(--folder-white);
  }
  .feature h2 {
    font-size: 11px; font-weight: 700; letter-spacing: 0.1px;
    margin-bottom: 13px; text-transform: uppercase;
  }
  .feature p {
    font-size: 9.3px; line-height: 12.4px; color: var(--body-on-blue);
    text-align: justify; margin-bottom: 12.4px;
  }
  .brace { position: absolute; left: 278px; }
  .project-photos {
    position: absolute; left: 75px; top: 570px;
    display: grid; grid-template-columns: 89px 89px; gap: 6px;
  }
  .project-photo { height: 66px; }
  .project-photo.tone-a { background: linear-gradient(160deg, var(--photo-tone-a), #6f7a80); }
  .project-photo.tone-b { background: linear-gradient(160deg, #eef1f2, var(--photo-tone-b)); }
  .pocket {
    position: absolute; left: 0; top: 0; width: 1090px; height: 772px;
  }
  .brand-name {
    position: absolute; left: 730px; top: 630px; width: 200px;
    text-align: center;
    font-size: 30px; font-weight: 400; color: var(--brand-blue);
    letter-spacing: 0.5px; line-height: 32px;
  }
  .brand-web {
    position: absolute; left: 746px; top: 691px;
    display: flex; align-items: center; gap: 7px;
    font-size: 17px; font-style: italic; color: var(--brand-blue);
  }
</style>
</head>
<body>
  <div class="folder">
    <section class="inside-panel">
      <div class="feature" style="left:74px; top:45px;">
        <h2>Solar Film</h2>
        <p>There are many benefits with our solar film products, they can help reduce the heat passing through your windows, reduce the glare often present on bright days, as well as reduce over 99% of the harmful ultraviolet rays that damage furnishings and cause skin damage.</p>
      </div>
      <div class="feature" style="left:307px; top:45px;">
        <h2>Protection from the Sun</h2>
        <p>Our solar film can remove as much as 79% of the sun's total energy. Utilizing advanced metals and ceramic technology, we can offer products with very low reflectivity and high light transmission levels as well reflective film for maximum heat rejection and privacy.</p>
      </div>

      <div class="feature" style="left:74px; top:243px;">
        <h2>Frosted Film</h2>
        <p>Once installed, frosted window film can increase your privacy, reduce the glare, or change a dated office environment to a more functional and appealing workplace.</p>
      </div>
      <div class="feature" style="left:307px; top:243px;">
        <h2>Increased Privacy</h2>
        <p>Whether you are an architect, interior designer or homeowner, we have the products for your creative side.</p>
        <p>Bring out your creative side with custom frosted graphics. With different shades of frost you can control the amount of light and privacy required, use patterns and textured frosted film to customize your graphics even more. By mixing the various products, your glass becomes a blank canvas with endless possibilities.</p>
      </div>

      <div class="feature" style="left:74px; top:454px;">
        <h2>Safety and Security Film</h2>
        <p>Ideal for glass where safety from potential injury is required or to delay the entry by an intruder.</p>
      </div>
      <div class="feature" style="left:307px; top:454px;">
        <h2>Peace of Mind</h2>
        <p>Optically Clear and Long Lasting</p>
        <p>The abundance of glass in homes and businesses offer a great deal of light and openness, with that comes a higher degree of risk for injury. Crime, vandalism, natural disasters and everyday accidents exist but with security film from Glazemark those dangers can be greatly reduced.</p>
        <p>Clearvane security film is available in a variety of thicknesses as well as varying tint levels, the different products are available as an optically clear film to a highly reflective solar film to help reduce the heat gain in the summer months as well increasing the privacy through those windows.</p>
      </div>

      <svg class="brace" style="top:43px;" width="8" height="66" viewBox="0 0 8 66" fill="none" stroke="#ffffff" stroke-width="1">
        <path d="M1 1 Q5 1 5 5 V29 Q5 33 8 33 Q5 33 5 37 V61 Q5 65 1 65"/>
      </svg>
      <svg class="brace" style="top:242px;" width="8" height="64" viewBox="0 0 8 64" fill="none" stroke="#ffffff" stroke-width="1">
        <path d="M1 1 Q5 1 5 5 V28 Q5 32 8 32 Q5 32 5 36 V59 Q5 63 1 63"/>
      </svg>
      <svg class="brace" style="top:453px;" width="8" height="66" viewBox="0 0 8 66" fill="none" stroke="#ffffff" stroke-width="1">
        <path d="M1 1 Q5 1 5 5 V29 Q5 33 8 33 Q5 33 5 37 V61 Q5 65 1 65"/>
      </svg>

      <div class="project-photos">
        <div class="project-photo tone-a" role="img" aria-label="Storefront with frosted window film"></div>
        <div class="project-photo tone-b" role="img" aria-label="Bright office interior with film on glass"></div>
        <div class="project-photo tone-b" role="img" aria-label="Frosted glass office partition"></div>
        <div class="project-photo tone-a" role="img" aria-label="Commercial building windows with tint"></div>
      </div>
    </section>

    <svg class="pocket" viewBox="0 0 1090 772" aria-hidden="true">
      <defs>
        <filter id="pocket-shadow" x="-10%" y="-20%" width="120%" height="140%">
          <feGaussianBlur stdDeviation="6"/>
        </filter>
      </defs>
      <polygon points="580,772 580,632 720,492 1090,492 1090,772" fill="#000" opacity="0.22" filter="url(#pocket-shadow)" transform="translate(-4,-2)"/>
      <polygon points="586,772 586,632 724,493 1090,493 1090,772" fill="#ffffff"/>
    </svg>

    <div class="brand-name">GLAZEMARK</div>
    <div class="brand-web">
      <svg width="13" height="13" viewBox="0 0 13 13" fill="none" stroke="#1a8fd0" stroke-width="1">
        <circle cx="6.5" cy="6.5" r="5.5"/>
        <ellipse cx="6.5" cy="6.5" rx="2.4" ry="5.5"/>
        <line x1="1" y1="6.5" x2="12" y2="6.5"/>
      </svg>
      <span>www.glazemark.ca</span>
    </div>
  </div>
</body>
</html>
```